HOME PAGE AND AND SECONDARY DESIGN FOR INTERNAL PAGES

Construction company looking for an easy to navagate professional serious greyscale website with a good clean feel simple clean menu and responsive friendly design. Our main clientele is commercial properties business owners and investors of rental properties. This website is going to be static HTML5 and would need multiple sizing files for clean fast rendering. Clean and accurate design files a must so if your experienced awesome modern greyscale designer let's get started I need this done as soon as possible.

Industry/Entity Type

construction, electrical, plumbing, commercial build outs

Number of Pages Required

2 page

Font styles to use
Sans Serif

Colors

Designer to choose only greyscale colors for use in the design.

Requirements
Must have
• Main Menu... Home, Services, Projects, About our team

```html
<!DOCTYPE html>
<html lang="en">
<head>
<meta charset="utf-8">
<title>Keystone Build of Texas LLC</title>
<link rel="stylesheet" href="https://fonts.googleapis.com/css2?family=Audiowide&family=Oxanium:wght@400;500;600&family=Mulish:wght@400;500&display=swap">
<style>
:root{
  --white:#ffffff;
  --ink:#4f5358;
  --ink-soft:#6a6e73;
  --band:#7d8288;
  --band-dark:#55595e;
  --footer:#6e7379;
  --light:#f2f2f2;
  --tab:#6b6f74;
  --btn:#5d6166;
  --photo-a:#9a9ea3;
  --photo-b:#4c5055;
}
*{margin:0;padding:0;box-sizing:border-box}
html,body{width:1200px;height:3242px;overflow:hidden;background:var(--white)}
body{position:relative;font-family:"Mulish",sans-serif;color:var(--ink)}
.abs{position:absolute}
.tech{font-family:"Oxanium",sans-serif}
.photo{background:linear-gradient(160deg,var(--photo-a),var(--photo-b))}

/* header */
.brand{left:132px;top:40px;width:170px;text-align:center;font-family:"Oxanium",sans-serif;font-weight:600;color:var(--ink)}
.brand-name{font-size:19px;letter-spacing:.5px;line-height:22px}
.brand-sub{font-size:11px;letter-spacing:3px;line-height:16px}
.contact-icon{width:28px;height:28px;background:var(--ink-soft);display:flex;align-items:center;justify-content:center}
.contact-label{font-family:"Oxanium",sans-serif;font-size:11px;color:var(--ink-soft);letter-spacing:.5px}
.contact-value{font-family:"Oxanium",sans-serif;color:var(--ink)}
.nav a{position:absolute;top:86px;font-family:"Oxanium",sans-serif;font-size:15px;font-weight:500;letter-spacing:.5px;color:var(--ink);text-decoration:none;white-space:nowrap}
.nav a.active{border-bottom:2px solid var(--ink);padding-bottom:4px}

/* hero */
.hero-title{left:0;width:1200px;top:306px;text-align:center;font-family:"Audiowide",sans-serif;font-size:36px;line-height:48px;color:var(--white);text-shadow:0 2px 6px rgba(0,0,0,.55)}
.btn{display:flex;align-items:center;justify-content:center;font-family:"Oxanium",sans-serif;font-weight:500;letter-spacing:.5px;white-space:nowrap}
.btn-white{background:var(--white);color:var(--ink);font-size:15px}
.btn-outline{border:1.5px solid var(--ink-soft);border-radius:6px;color:var(--ink);font-size:13px;background:var(--white)}
.btn-dark{background:var(--btn);color:var(--white);border-radius:5px;font-size:12px}
.dot{width:11px;height:11px;border-radius:50%;border:1.5px solid var(--white)}
.dot.on{background:var(--white)}

.section-title{left:0;width:1200px;text-align:center;font-family:"Oxanium",sans-serif;font-weight:500;font-size:21px;letter-spacing:1px;color:var(--ink)}
.dash{width:22px;height:2px;background:var(--ink);left:589px}

/* service cards */
.service-card{background:var(--white);box-shadow:0 2px 10px rgba(0,0,0,.12);border-radius:4px;overflow:hidden}
.service-tab{background:var(--tab);color:var(--white);font-family:"Oxanium",sans-serif;font-size:16px;letter-spacing:.5px;border-radius:10px;display:flex;align-items:center;justify-content:center}
.service-text{font-size:14px;line-height:20px;text-align:center;color:var(--ink)}

/* about */
.about-title{left:651px;top:1326px;font-family:"Oxanium",sans-serif;font-weight:600;font-size:22px;letter-spacing:1px;color:var(--white)}
.about-text{left:651px;top:1408px;width:418px;font-size:14.5px;line-height:20.8px;text-align:justify;color:var(--white)}

/* team */
.team-card{background:var(--white);box-shadow:0 2px 10px rgba(0,0,0,.12);border-top:8px solid var(--tab);border-radius:5px 5px 3px 3px}
.team-photo{width:158px;height:158px;border-radius:50%}
.team-name{font-family:"Oxanium",sans-serif;font-size:17px;letter-spacing:1px;color:var(--ink);text-align:center}
.team-role{font-size:12.5px;color:var(--ink);text-align:center}
.team-text{font-size:12px;line-height:16px;color:var(--ink-soft);text-align:center}

/* projects */
.project-img{border-radius:4px}
.project-label{font-family:"Oxanium",sans-serif;font-size:13px;letter-spacing:1px;color:var(--ink-soft);text-align:center}

/* footer */
.footer-brand{left:131px;top:3044px;width:244px;text-align:center;font-family:"Oxanium",sans-serif;font-weight:600;color:var(--white)}
.footer-line{font-size:14px;color:var(--white);display:flex;align-items:center;gap:14px}
.footer-nav a{position:absolute;top:3078px;font-family:"Oxanium",sans-serif;font-size:14px;font-weight:500;letter-spacing:.5px;color:var(--white);text-decoration:none;white-space:nowrap}
.copyright{left:0;width:1200px;top:3183px;text-align:center;font-size:11px;color:var(--white)}
</style>
</head>
<body>

<!-- Header -->
<header>
  <div class="abs brand">
    <div class="brand-name">KEYSTONE BUILD</div>
    <div class="brand-sub">OF TEXAS LLC</div>
  </div>

  <div class="abs contact-icon" style="left:546px;top:28px">
    <svg width="12" height="10" viewBox="0 0 12 10"><rect x="0.5" y="0.5" width="11" height="9" fill="#fff"/><path d="M0.5 0.5 6 5 11.5 0.5" stroke="#6a6e73" fill="none"/></svg>
  </div>
  <div class="abs contact-label" style="left:589px;top:25px">EMAIL US</div>
  <div class="abs contact-value" style="left:589px;top:44px;font-size:14px">info@keystonebuildtx.com</div>

  <div class="abs contact-icon" style="left:855px;top:28px">
    <svg width="12" height="12" viewBox="0 0 24 24"><path fill="#fff" d="M6.6 10.8a15.1 15.1 0 0 0 6.6 6.6l2.2-2.2c.3-.3.7-.4 1-.2 1.1.4 2.3.6 3.6.6.6 0 1 .4 1 1V20c0 .6-.4 1-1 1A17 17 0 0 1 3 4c0-.6.4-1 1-1h3.5c.6 0 1 .4 1 1 0 1.3.2 2.5.6 3.6.1.3 0 .7-.2 1z"/></svg>
  </div>
  <div class="abs contact-label" style="left:895px;top:22px">CALL US</div>
  <div class="abs contact-value" style="left:895px;top:39px;font-size:20px;font-weight:500;letter-spacing:1px">512 - 555 - 0142</div>

  <nav class="nav">
    <a class="active" href="#" style="left:544px">HOME</a>
    <a href="#" style="left:642px">SERVICES</a>
    <a href="#" style="left:776px">PROJECTS</a>
    <a href="#" style="left:920px">ABOUT OUR TEAM</a>
  </nav>
</header>

<!-- Hero -->
<section>
  <svg class="abs" style="left:0;top:127px" width="1200" height="545" viewBox="0 0 1200 545">
    <defs>
      <linearGradient id="heroSky" x1="0" y1="0" x2="0" y2="1">
        <stop offset="0" stop-color="#9fa3a8"/>
        <stop offset=".55" stop-color="#6c7075"/>
        <stop offset="1" stop-color="#3e4146"/>
      </linearGradient>
    </defs>
    <rect width="1200" height="545" fill="url(#heroSky)" role="img" aria-label="Aerial photo of a downtown city skyline at dusk"/>
    <path d="M0 427 Q560 642 1200 400 L1200 545 L0 545Z" fill="#55595e"/>
    <path d="M0 442 Q560 656 1200 414 L1200 545 L0 545Z" fill="#ffffff"/>
  </svg>
  <h1 class="abs hero-title">WELCOME TO<br>KEYSTONE BUILD OF TEXAS</h1>
  <a class="abs btn btn-white" href="#" style="left:535px;top:424px;width:130px;height:36px;text-decoration:none">READ MORE</a>
  <div class="abs dot" style="left:568px;top:577px"></div>
  <div class="abs dot on" style="left:586px;top:577px"></div>
  <div class="abs dot" style="left:604px;top:577px"></div>
  <div class="abs dot" style="left:620px;top:577px"></div>
</section>

<!-- Services -->
<section>
  <h2 class="abs section-title" style="top:698px">OUR SERVICES</h2>
  <div class="abs dash" style="top:744px"></div>

  <article class="abs service-card" style="left:131px;top:789px;width:456px;height:430px">
    <svg width="456" height="226" viewBox="0 0 456 226" role="img" aria-label="Photo of a single-storey brick commercial building">
      <defs><linearGradient id="svc1" x1="0" y1="0" x2="0" y2="1"><stop offset="0" stop-color="#8e9297"/><stop offset="1" stop-color="#4f5358"/></linearGradient></defs>
      <path d="M0 0 H456 V206 Q228 240 0 206Z" fill="url(#svc1)"/>
    </svg>
    <div class="abs service-tab" style="left:97px;top:228px;width:262px;height:52px">COMMERCIAL PROPERTY</div>
    <p class="abs service-text" style="left:30px;top:300px;width:396px">There are many variations of passages of Lorem Ipsum available but the majority have suffered alteration</p>
    <a class="abs btn btn-outline" href="#" style="left:167px;top:364px;width:120px;height:34px;text-decoration:none">READ MORE</a>
  </article>

  <article class="abs service-card" style="left:613px;top:789px;width:455px;height:430px">
    <svg width="455" height="226" viewBox="0 0 455 226" role="img" aria-label="Photo of a multi-storey apartment building with balconies">
      <defs><linearGradient id="svc2" x1="0" y1="0" x2="0" y2="1"><stop offset="0" stop-color="#b4b7bb"/><stop offset="1" stop-color="#45494e"/></linearGradient></defs>
      <path d="M0 0 H455 V206 Q228 240 0 206Z" fill="url(#svc2)"/>
    </svg>
    <div class="abs service-tab" style="left:112px;top:228px;width:235px;height:52px">RENTAL PROPERTIES</div>
    <p class="abs service-text" style="left:30px;top:300px;width:396px">There are many variations of passages of Lorem Ipsum available but the majority have suffered alteration</p>
    <a class="abs btn btn-outline" href="#" style="left:167px;top:364px;width:120px;height:34px;text-decoration:none">READ MORE</a>
  </article>
</section>

<!-- About -->
<section>
  <svg class="abs" style="left:0;top:1275px" width="1200" height="525" viewBox="0 0 1200 525">
    <rect width="1200" height="525" fill="#7d8288"/>
    <path d="M0 393 Q600 615 1200 393 V525 H0Z" fill="#55595e"/>
    <path d="M0 408 Q600 630 1200 408 V525 H0Z" fill="#ffffff"/>
  </svg>
  <div class="abs photo" style="left:131px;top:1331px;width:467px;height:343px;border-radius:3px" role="img" aria-label="Photo of construction workers in hard hats in front of scaffolding"></div>
  <h2 class="abs about-title">ABOUT US</h2>
  <div class="abs" style="left:651px;top:1372px;width:24px;height:2px;background:var(--white)"></div>
  <p class="abs about-text">Sed ut perspiciatis unde omnis iste natus error sit voluptatem accusantium doloremque laudantium, totam rem aperiam, eaque ipsa quae ab illo inventore veritatis et quasi architecto beatae vitae dicta sunt explicabo. Nemo enim ipsam voluptatem quia voluptas sit aspernatur aut odit aut fugit, sed quia consequuntur magni dolores eos qui ratione voluptatem sequi nesciunt. Neque porro quisquam est, qui dolorem ipsum quia dolor sit amet, consectetur, adipisci velit, sed quia non numquam eius modi tempora incidunt ut labore et dolore magnam aliquam quaerat voluptatem.</p>
  <a class="abs btn btn-white" href="#" style="left:656px;top:1647px;width:118px;height:33px;border-radius:5px;font-size:13px;text-decoration:none">READ MORE</a>
</section>

<!-- Team -->
<section>
  <h2 class="abs section-title" style="top:1827px">OUR TEAM</h2>
  <div class="abs dash" style="top:1872px"></div>

  <article class="abs team-card" style="left:131px;top:1988px;width:295px;height:370px">
    <div class="abs team-photo photo" style="left:68px;top:-67px" role="img" aria-label="Portrait photo of Daniel"></div>
    <h3 class="abs team-name" style="left:0;width:295px;top:122px">DANIEL</h3>
    <div class="abs team-role" style="left:0;width:295px;top:145px">Managing Director</div>
    <p class="abs team-text" style="left:42px;width:211px;top:185px">Sed ut perspiciatis unde omnis iste natus error sit voluptatem accus antium doloremque laudantium, totam rem aperiam, eaque ipsa quae ab illo inventore veritatis et quasi architecto beatae vitae</p>
    <a class="abs btn btn-dark" href="#" style="left:96px;top:298px;width:104px;height:29px;text-decoration:none">READ MORE</a>
  </article>

  <article class="abs team-card" style="left:449px;top:1988px;width:295px;height:370px">
    <div class="abs team-photo photo" style="left:68px;top:-67px" role="img" aria-label="Portrait photo of Marcus"></div>
    <h3 class="abs team-name" style="left:0;width:295px;top:122px">MARCUS</h3>
    <div class="abs team-role" style="left:0;width:295px;top:145px">Managing Director</div>
    <p class="abs team-text" style="left:42px;width:211px;top:185px">Sed ut perspiciatis unde omnis iste natus error sit voluptatem accus antium doloremque laudantium, totam rem aperiam, eaque ipsa quae ab illo inventore veritatis et quasi architecto beatae vitae</p>
    <a class="abs btn btn-dark" href="#" style="left:96px;top:298px;width:104px;height:29px;text-decoration:none">READ MORE</a>
  </article>

  <article class="abs team-card" style="left:772px;top:1988px;width:296px;height:370px">
    <div class="abs team-photo photo" style="left:69px;top:-67px" role="img" aria-label="Portrait photo of Oliver"></div>
    <h3 class="abs team-name" style="left:0;width:296px;top:122px">OLIVER</h3>
    <div class="abs team-role" style="left:0;width:296px;top:145px">Managing Director</div>
    <p class="abs team-text" style="left:42px;width:212px;top:185px">Sed ut perspiciatis unde omnis iste natus error sit voluptatem accus antium doloremque laudantium, totam rem aperiam, eaque ipsa quae ab illo inventore veritatis et quasi architecto beatae vitae</p>
    <a class="abs btn btn-dark" href="#" style="left:96px;top:298px;width:104px;height:29px;text-decoration:none">READ MORE</a>
  </article>
</section>

<!-- Projects -->
<section>
  <div class="abs" style="left:0;top:2414px;width:1200px;height:400px;background:var(--light)"></div>
  <h2 class="abs section-title" style="top:2451px">PROJECTS</h2>
  <div class="abs dash" style="top:2498px"></div>

  <svg class="abs" style="left:70px;top:2622px" width="18" height="32" viewBox="0 0 18 32"><path d="M15 2 3 16 15 30" stroke="#8a8e93" stroke-width="2.5" fill="none"/></svg>
  <svg class="abs" style="left:1110px;top:2622px" width="18" height="32" viewBox="0 0 18 32"><path d="M3 2 15 16 3 30" stroke="#8a8e93" stroke-width="2.5" fill="none"/></svg>

  <div class="abs project-img photo" style="left:131px;top:2538px;width:227px;height:210px" role="img" aria-label="Photo of a retail strip building"></div>
  <div class="abs project-img photo" style="left:366px;top:2538px;width:226px;height:210px" role="img" aria-label="Photo of a modern apartment block with balconies"></div>
  <div class="abs project-img photo" style="left:603px;top:2538px;width:227px;height:210px" role="img" aria-label="Photo of a white residential building"></div>
  <div class="abs project-img photo" style="left:842px;top:2538px;width:227px;height:210px" role="img" aria-label="Photo of a dark glass office building"></div>

  <div class="abs project-label" style="left:131px;width:227px;top:2763px">PROJECT 1</div>
  <div class="abs project-label" style="left:366px;width:226px;top:2763px">PROJECT 2</div>
  <div class="abs project-label" style="left:603px;width:227px;top:2763px">PROJECT 3</div>
  <div class="abs project-label" style="left:842px;width:227px;top:2763px">PROJECT 4</div>
</section>

<!-- Footer -->
<footer>
  <svg class="abs" style="left:0;top:2780px" width="1200" height="462" viewBox="0 0 1200 462">
    <rect width="1200" height="462" fill="#6e7379"/>
    <path d="M0 0 H1200 V30 Q600 236 0 30Z" fill="#55595e"/>
    <path d="M0 0 H1200 V18 Q600 214 0 18Z" fill="#f2f2f2"/>
  </svg>
  <a class="abs btn btn-dark" href="#" style="left:512px;top:2819px;width:160px;height:28px;text-decoration:none">VIEW ALL PROJECTS</a>

  <div class="abs footer-brand">
    <div style="font-size:25px;letter-spacing:1px;line-height:30px">KEYSTONE BUILD</div>
    <div style="font-size:15px;letter-spacing:4px;line-height:22px">OF TEXAS LLC</div>
  </div>
  <div class="abs" style="left:446px;top:2958px;width:1px;height:139px;background:rgba(255,255,255,.7)"></div>

  <div class="abs footer-line" style="left:527px;top:2959px">
    <svg width="10" height="13" viewBox="0 0 10 13"><path d="M5 0a5 5 0 0 0-5 5c0 3.5 5 8 5 8s5-4.5 5-8a5 5 0 0 0-5-5zm0 7a2 2 0 1 1 0-4 2 2 0 0 1 0 4z" fill="#fff"/></svg>
    <span>4100 Ridgeline Drive STE 200,&nbsp; Austin, Texas 78731</span>
  </div>
  <div class="abs footer-line" style="left:527px;top:2993px">
    <svg width="10" height="10" viewBox="0 0 24 24"><path fill="#fff" d="M6.6 10.8a15.1 15.1 0 0 0 6.6 6.6l2.2-2.2c.3-.3.7-.4 1-.2 1.1.4 2.3.6 3.6.6.6 0 1 .4 1 1V20c0 .6-.4 1-1 1A17 17 0 0 1 3 4c0-.6.4-1 1-1h3.5c.6 0 1 .4 1 1 0 1.3.2 2.5.6 3.6.1.3 0 .7-.2 1z"/></svg>
    <span>512 - 555 - 0142</span>
  </div>
  <div class="abs footer-line" style="left:527px;top:3027px">
    <svg width="10" height="8" viewBox="0 0 12 10"><rect x="0.5" y="0.5" width="11" height="9" fill="#fff"/><path d="M0.5 0.5 6 5 11.5 0.5" stroke="#6e7379" fill="none"/></svg>
    <span>info@keystonebuildtx.com</span>
  </div>

  <nav class="footer-nav">
    <a href="#" style="left:526px">HOME</a>
    <a href="#" style="left:627px">SERVICES</a>
    <a href="#" style="left:765px">PROJECTS</a>
    <a href="#" style="left:912px">ABOUT OUR TEAM</a>
  </nav>

  <div class="abs" style="left:131px;top:3139px;width:934px;height:1px;background:rgba(255,255,255,.6)"></div>
  <p class="abs copyright">Copyright © 2023 All Rights Reserved</p>
</footer>

</body>
</html>
```